Wine Bottle Label for Tall Fern Wines

We are a small, newly established winery in need of an original, bold and outstanding bottle label design for our Tall Fern wine.

Our vineyard and winery are located on a 200 acre farm in a remote part of southern Oregon. The name "Tall Fern" was inspired by the large, overgrown size of all of the foliage here, including our grapevines. Things grow large and vigorous in Oregon! And everything is very lush and green. It is almost surreal or other-worldly, like the landscapes seen in the Keeper of The Stones movies, or the land of Quill. It is a place that makes you say "wow" with its epic, large scale, natural beauty.

The name "Tall Fern" also captures the essence of our wine. It is big in flavor, quality and color. Our first release is a Pinot Noir (red). Pinot Noir wines often are subtle in flavor and thin in their color. Our label should convey that our Pinot Noir is a much more robust, darker, heavier, meatier, more flavorful wine that is a lot more fun than an "ordinary" wine. At the same time, this wine is not cheap, and so nothing in the label should convey "bargain," "low price," or "cheapness." This is a fine wine with a sense of adventure. Be sure to convey "quality" with your design along with "big," "adventure" and "fun".

The label should appeal to a younger demographic, both male and female, between the ages of 21 and 35. It should be non-traditional and adventurous and suggest a pushing of boundaries and a breaking of rules. This Pinot Noir does not conform to the normal "limitations" of the variety, therefore the label should not conform. It should have an "organic" or "natural" or "agricultural" vibe, as opposed to something mechanical or technical. It should, however, be contemporary. Do not confuse "natural" or "organic" with being nostalgic or old school. Think "agri-hipsters."

The label should be designed to fit on a Burgundy-style wine bottle (photo attached for reference). (Note: All Pinot Noir and Chardonnay is bottled in Burgundy bottles, If you are not sure about the bottle shape you can go to a local store and compare the various bottles. Locate a bottle of Pinot Noir or Chardonnay or anything identified as a "Burgundy Wine," and it should be the correct bottle. The tall, skinny bottles used for Cabernet Sauvignon are NOT correct)). Please see the "Must Have" notes for more on the bottle.

In summary, the final project should be a wine bottle label design that conveys bigness, vastness, adventurous, non-traditional, high quality wine. A good tagline to keep in mind is "Living Large."

Target Market(s)

Young, hip, non-conformist wine drinkers aged 21-35 with a sense of adventure and an appreciation of quality.

Industry/Entity Type

School

Requirements
Must have
• *Must contain the words:

Tall Fern (the brand)
2013 Pinot Noir (the vintage year and variety)

*The label must be designed to fit a Burgundy-style wine bottle. A photo is attached for reference.

*Additionally, the label needs to fit on the lower, widest part of the bottle. The label will be printed on sticky paper and rolled onto the bottle with a machine. The machine cannot apply labels to the neck of the bottle. The maximum size of a label that will fit this space is 5.5 inches wide by 4.5 inches tall. You DO NOT have to fill ALL of this space or confine the label shape to a rectangle, but the label cannot exceed this size or it won't stick to the bottle properly. It will really help if you can put your hands on an actual bottle to see the logistics of applying the label. But if that is not possible, just do your best with the instructions you have. I am confident the winning design could be adjusted to fit the bottle, if necessary
Nice to have
• *Wine grape leaf or leaves.

*A concept I have been playing with is sunlight shining through leaves like light through a Marlowe lamp or a stained glass window. This is NOT a requirement for this label. However, if the concept inspires and idea, I would be most happy to see it.
Should not have
• IF a leaf or leaves are included in the design (not a requirement) they MUST be wine grapevine leafs and preferably leaves of the Pinot Noir vine. Do not use generic leaves or identifiable leaves such as oak leaves, maple leaves, or anything that looks like the Canadian flag or the Halden Ridge Ravens hockey logo. Reference the attached photos of wine grape leaves to see the correct leaf type. I am happy to email more photos upon request. These photos may be used in whole or in part in your design, however, a leaf from a photo is NOT a requirement, nor is the image of a leaf or leaves.

This label should NOT be designed for Bordeaux-style wine bottles (the tall, skinny ones).

```html
<!DOCTYPE html>
<html lang="en">
<head>
<meta charset="utf-8">
<title>Tall Fern Pinot Noir Label</title>
<link rel="stylesheet" href="https://fonts.googleapis.com/css2?family=Bebas+Neue&family=Oswald:wght@300&display=swap">
<style>
  :root {
    --wine-red: #8a0404;
    --paper: #ffffff;
    --canvas: #ffffff;
  }
  html, body {
    margin: 0;
    padding: 0;
    width: 1200px;
    height: 997px;
    overflow: hidden;
    background: var(--canvas);
  }
  .label {
    display: block;
    width: 1200px;
    height: 997px;
  }
  .label-body { fill: var(--wine-red); }
  .label-frame { fill: none; stroke: var(--paper); stroke-width: 1.6; }
  .leaf-area { fill: var(--paper); }
  .name-band { fill: var(--wine-red); }
  .band-rule { stroke: var(--paper); stroke-width: 3; }
  .region {
    font-family: "Bebas Neue", sans-serif;
    font-size: 37px;
    letter-spacing: 4px;
    fill: var(--paper);
  }
  .vintage {
    font-family: "Bebas Neue", sans-serif;
    font-size: 50px;
    letter-spacing: 2px;
    fill: var(--paper);
  }
  .brand-name {
    font-family: "Bebas Neue", sans-serif;
    font-size: 90px;
    letter-spacing: 11px;
    fill: var(--paper);
  }
  .variety {
    font-family: "Bebas Neue", sans-serif;
    font-size: 35px;
    letter-spacing: 8px;
    fill: var(--wine-red);
  }
  .legal {
    font-family: "Oswald", sans-serif;
    font-weight: 300;
    font-size: 21px;
    letter-spacing: -0.5px;
    fill: var(--paper);
  }
</style>
</head>
<body>
<svg class="label" viewBox="0 0 1200 997" xmlns="http://www.w3.org/2000/svg">
  <path class="label-body"
        d="M232,167 H948 A37,37 0 0 0 985,204 V775 A37,37 0 0 0 948,812 H232 A37,37 0 0 0 195,775 V204 A37,37 0 0 0 232,167 Z"/>
  <path class="label-frame"
        d="M241,177 H939 A34,34 0 0 0 975,213 V766 A34,34 0 0 0 939,802 H241 A34,34 0 0 0 205,766 V213 A34,34 0 0 0 241,177 Z"/>

  <g role="img" aria-label="Large white grapevine leaf silhouette with its stem">
    <ellipse class="leaf-area" cx="590" cy="537" rx="240" ry="237"/>
  </g>

  <text class="region" x="250" y="249">BRIARVALE</text>
  <text class="region" x="931" y="249" text-anchor="end">OREGON</text>

  <rect class="name-band" x="312" y="418" width="556" height="94"/>
  <line class="band-rule" x1="312" y1="418" x2="868" y2="418"/>
  <line class="band-rule" x1="312" y1="512" x2="868" y2="512"/>

  <text class="vintage" x="339" y="484" text-anchor="middle">20</text>
  <text class="brand-name" x="597" y="497" text-anchor="middle">TALL FERN</text>
  <text class="vintage" x="845" y="484" text-anchor="middle">13</text>

  <text class="variety" x="593" y="556" text-anchor="middle">-PINOT NOIR-</text>

  <text class="legal" x="252" y="755">ALC. 12.5% BY VOL.</text>
  <text class="legal" x="928" y="755" text-anchor="end">750 ML ℮</text>
</svg>
</body>
</html>
```